Brindlemark Group information card

We need a 5x7 two-sided card to hand out at open houses and provide to our charitable partners for distribution. We are a local real estate group looking to add a "give back" component to our business. We are located in a coastal community and would like to incorporate that feel into our design. We are giving clients who use us the ability to designate 1 out of the 10 charitable organizations we partner with - and we will make a donation to that organization.

We included the 10 partner logos below - we envision them pretty small. Also included 2 photos of the "Brindlemark" and our logo. Have fun.
Updates

Target Market(s)

home buyers & sellers

Industry/Entity Type

Real Estate

Font styles to use
Serif
Sans Serif

Colors

Designer to choose colors to be used in the design.

Requirements
Must have
• slogan & tagline - see attached text file
• Brindlemark photo
Nice to have
• partner logos - small - maybe in circles?

```html
<!DOCTYPE html>
<html lang="en">
<head>
<meta charset="utf-8">
<title>Brindlemark Group – We Live Here. We Give Here.</title>
<link rel="stylesheet" href="https://fonts.googleapis.com/css2?family=Josefin+Sans:wght@600;700&family=Questrial&display=swap">
<style>
  :root {
    --navy: #3d5a8c;
    --chevron: #5b86c8;
    --accent: #5d88c9;
    --ink: #222428;
    --name-ink: #1b2440;
    --black: #0b0b0b;
    --white: #ffffff;
    --shadow: #d9dde3;
  }
  * { margin: 0; padding: 0; box-sizing: border-box; }
  html, body { width: 857px; height: 1200px; overflow: hidden; background: var(--white); }
  .card { position: relative; width: 857px; height: 1200px; overflow: hidden; background: var(--white); }

  .headline {
    position: absolute; right: 36px; top: 30px;
    font-family: "Josefin Sans", sans-serif; font-weight: 600;
    font-size: 64px; line-height: 74px; color: var(--navy);
    text-align: right; letter-spacing: -0.5px; white-space: nowrap;
  }

  .hero { position: absolute; left: 0; top: 0; width: 857px; height: 850px; }

  .brand {
    position: absolute; left: 495px; top: 320px; width: 260px;
    text-align: center; color: var(--white);
    font-family: "Questrial", sans-serif; font-size: 36px; line-height: 40px;
    white-space: nowrap;
  }

  .intro {
    position: absolute; left: 33px; top: 852px; width: 553px;
    font-family: "Questrial", sans-serif; font-size: 18px; line-height: 26px;
    letter-spacing: 0.3px; color: var(--ink); text-align: justify;
  }
  .intro p + p { margin-top: 6px; }

  .tagline {
    position: absolute; left: 605px; top: 858px; width: 248px;
    font-family: "Josefin Sans", sans-serif; font-weight: 600;
    font-size: 30px; line-height: 32px; color: var(--accent);
    text-align: center; white-space: nowrap;
  }

  .footer-bar { position: absolute; left: 0; top: 1150px; width: 857px; height: 50px; background: var(--black); }

  .contact {
    position: absolute; left: 605px; top: 1033px; width: 232px; height: 167px;
    background: var(--chevron); text-align: center; padding-top: 24px;
  }
  .contact-name {
    font-family: "Josefin Sans", sans-serif; font-weight: 700;
    font-size: 27px; line-height: 28px; color: var(--name-ink);
    white-space: nowrap;
  }
  .contact-email {
    font-family: "Questrial", sans-serif; font-size: 14.5px; line-height: 20px;
    color: var(--white); white-space: nowrap; margin-bottom: 26px;
  }
</style>
</head>
<body>
<div class="card">
  <svg class="hero" viewBox="0 0 857 850" xmlns="http://www.w3.org/2000/svg">
    <defs>
      <linearGradient id="coast-tones" x1="0" y1="0" x2="0" y2="1">
        <stop offset="0" stop-color="#6f9fd6"/>
        <stop offset="0.45" stop-color="#dfe8f0"/>
        <stop offset="0.56" stop-color="#6f95b0"/>
        <stop offset="0.72" stop-color="#9a9c8c"/>
        <stop offset="0.86" stop-color="#4f5f3e"/>
        <stop offset="1" stop-color="#9b3a33"/>
      </linearGradient>
    </defs>
    <polygon class="chevron-shadow" points="640,190 830,415 815,425 630,200" fill="var(--shadow)"/>
    <polygon class="chevron-band" points="405,225 815,225 815,418 540,840 0,840 0,810 500,810 665,578" fill="var(--chevron)"/>
    <polygon class="coast-photo" role="img" aria-label="Coastal town view overlooking the bay, pier and blue sky with red shrubs in the foreground"
      points="0,225 380,225 640,578 490,793 0,793" fill="url(#coast-tones)"/>
    <g class="partner-badges" role="img" aria-label="Partner organization badges">
      <circle cx="810" cy="535" r="30" fill="#8b7a95"/>
      <circle cx="735" cy="625" r="30" fill="#3f6a5a"/>
      <circle cx="810" cy="625" r="30" fill="#6b4a35"/>
      <circle cx="658" cy="712" r="30" fill="#0d0d0d"/>
      <circle cx="735" cy="712" r="30" fill="#ffffff" stroke="#cfd6dd"/>
      <circle cx="810" cy="712" r="30" fill="#d92a2a"/>
      <circle cx="582" cy="802" r="30" fill="#ffffff" stroke="#cfd6dd"/>
      <circle cx="658" cy="802" r="30" fill="#ffffff" stroke="#cfd6dd"/>
      <circle cx="735" cy="802" r="30" fill="#e58bb8"/>
      <circle cx="810" cy="802" r="30" fill="#111111"/>
    </g>
  </svg>

  <h1 class="headline">WE LIVE HERE.<br>WE GIVE HERE.</h1>

  <div class="brand">Brindlemark<br>Group</div>

  <div class="intro">
    <p>We give because we value generosity and believe we have been blessed to be a blessing.</p>
    <p>We believe that together we can changethe world one home at time. You have our guarantee of personal service and no additional costs. The donations come out of our commission, not your pocket. You get to designate which of our amazing partner organizations you would like us to contribute to on behalf of your transaction. When you are ready to buy or sell, please consider giving us a call. Tell a friend about us too.</p>
  </div>

  <div class="tagline">TOGETHER,<br>WE CAN<br>MAKE THE<br>WORLD A<br>BETTER PLACE.</div>

  <div class="footer-bar"></div>

  <div class="contact">
    <div class="contact-name">OWEN HALE</div>
    <div class="contact-email">owen@brindlemarkgroup.com</div>
    <div class="contact-name">LENA HALE</div>
    <div class="contact-email">lena@brindlemarkgroup.com</div>
  </div>
</div>
</body>
</html>
```